Tuition Center Website

We need a new web site for a tutoring company based in sydney.

We only teach senior highschool students and pride ourselves on building the students abilities to think their way through life.

I would like a bright and vibrant website that looks professional and modern.
It needs to look simple and neat but also have the functionality we need.
Images and flash would be good.

Please keep in mind that the site must be appealing to a younger audience.

We need a multipage website with the following navigation bars:

1.Home (As logo not "home" button)
I would like a news box/ticker somewhere that can stream our chatterbook and pipstream feeds and also any news updates we want to put up.
Subscribe to newsletter button.

2. About us.
This needs to be a pull down into:
-What we do
-Why we do it
-How we do it

3. Courses
Pulldown into:
-Maths
-English
-Science
(we may need to attach extra pages behind these e.g. Courses/Science/Physics or Courses/Science/Chemistry and possibly add a link to a new zandlo form)

4. Inspired
This page is like a blog page where we can upload videos, links to articles that we find to be inspiring and hopefully will inspire others.

5. Inspire
This is a recruitment page. Only content here.

6. Contact us.
Mapquill map widget and a 'contact us' form

* Our branding requires green close to #12FF3D

***Please have a look at the current website.
@ www.velmorlearning.com.au

Thanks everybody hope the revision of my brief is better and more informative than my last one

Target Market(s)

senior highschool students aged 15-19, parents ( to a lesser degree)

Industry/Entity Type

It Company

Requirements
Must have
• Ability to change content on pages.

The green doesn't have to be everywhere, but it must be obvious that it is our colour.

Nice to have
• Sites with a nicer mix of images and flash will be given more consideration. But then again, if you amaze us, you amaze us and we will go with your design.
Should not have
• Should stay away from ocre, brown colours and serif fonts.

```html
<!DOCTYPE html>
<html lang="en">
<head>
<meta charset="utf-8">
<title>Velmor Learning – HSC Coaching &amp; Mentoring</title>
<link href="https://fonts.googleapis.com/css2?family=Rosario:wght@400;700&family=Open+Sans:wght@400;600;700&display=swap" rel="stylesheet">
<style>
:root{
  --brand-green:#86ae00;
  --link-green:#8cc000;
  --accent-blue:#4cb8d8;
  --ink:#2f2f2f;
  --text-grey:#7c7c7c;
  --rule:#dedede;
  --nav-active:#3a4150;
  --band-grey:#efefef;
  --footer:#303030;
  --footer-base:#232323;
  --footer-text:#a9a9a9;
}
*{box-sizing:border-box;margin:0;padding:0}
html,body{width:963px;height:1200px;overflow:hidden;background:#fff}
body{position:relative;font-family:"Open Sans",sans-serif;color:var(--text-grey)}
.abs{position:absolute}
a{color:inherit;text-decoration:none}

/* header */
.topline{left:0;top:0;width:963px;height:3px;background:var(--ink)}
.brand{left:120px;top:24px;display:flex;align-items:center;gap:8px}
.brand-mark{width:30px;height:30px;background:var(--brand-green)}
.brand-name{font-family:"Rosario",sans-serif;font-size:17px;font-weight:700;color:var(--ink);line-height:1.05;width:70px}
.main-nav{left:450px;top:49px;display:flex;align-items:center;font-family:"Rosario",sans-serif;font-size:12.5px;color:#444}
.main-nav a{padding:4px 12.5px}
.main-nav a.current{background:var(--nav-active);color:#fff;border-radius:3px;font-weight:700;padding:5px 13px;margin-right:0}

/* hero */
.hero{left:0;top:96px;width:963px;height:315px;background:var(--brand-green);border-top:1px solid #7a9e00;border-bottom:1px solid #779a00}
.hero h1{position:absolute;left:118px;top:50px;font-family:"Rosario",sans-serif;font-weight:400;font-size:44px;color:var(--ink);letter-spacing:-.5px}
.hero h2{position:absolute;left:119px;top:100px;font-family:"Rosario",sans-serif;font-weight:400;font-size:17.5px;color:#1f1f1f}
.hero p{position:absolute;left:118px;top:128px;width:405px;font-family:"Rosario",sans-serif;font-size:12.2px;line-height:16px;color:#fff}
.btn-enquire{position:absolute;left:119px;top:211px;width:108px;height:32px;background:linear-gradient(#2e2e2e,#0c0c0c);border-radius:3px;color:#fff;font-family:"Rosario",sans-serif;font-size:14px;display:flex;align-items:center;justify-content:center;box-shadow:0 1px 2px rgba(0,0,0,.3)}
.hero-art{position:absolute;left:575px;top:14px;width:225px;height:262px;border-radius:8px;background:radial-gradient(circle at 50% 45%,#a8c83a,#8cb20a 70%)}
.slider-dots{position:absolute;left:461px;top:290px;display:flex;gap:8px}
.slider-dots span{width:8px;height:8px;border-radius:50%;background:#1e1e1e}
.slider-dots span.on{background:#fff}

/* section titles */
.sec-title{font-family:"Rosario",sans-serif;font-weight:400;font-size:17.5px;color:var(--ink);text-transform:uppercase}
.title-rule{height:2px;background:var(--rule)}
.title-rule::before{content:"";display:block;width:30px;height:3px;margin-top:-1px;background:var(--accent-blue)}

/* welcome */
.welcome-copy{left:106px;top:494px;width:480px;font-size:10px;line-height:17px}
.btn-register{left:106px;top:580px;width:90px;height:25px;border-radius:3px;background:linear-gradient(#fafafa,#e4e4e4);border:1px solid #d6d6d6;font-family:"Rosario",sans-serif;font-size:11px;color:#444;display:flex;align-items:center;justify-content:center}
.welcome-photo{left:610px;top:490px;width:233px;height:111px;background:linear-gradient(110deg,#4f7f8a,#2f4d63 45%,#c9d6d2)}
.divider{left:0;top:641px;width:963px;height:1px;background:#e6e6e6}

/* columns */
.col-text{font-size:9.9px;line-height:16px}
.student-photo{left:106px;top:723px;width:57px;height:57px;background:linear-gradient(#7a5a4a,#c08d72);}
.quote-by{font-size:10px;color:#555}
.quote-by b{color:#333;font-weight:600}
.trial-box{left:362px;top:722px;width:234px;height:56px;background:var(--ink);border:1px solid #1a1a1a;font-family:"Rosario",sans-serif;color:#fff}
.trial-box .l1{position:absolute;left:10px;top:7px;font-size:15px}
.trial-box .l2{position:absolute;right:10px;top:25px;font-size:15px}
.trial-box em{font-family:"Open Sans",sans-serif;font-weight:700;font-size:17.5px;color:var(--link-green)}
.send-link{font-family:"Rosario",sans-serif;font-size:11px;color:#333}
.news-item{left:618px;width:238px;height:85px}
.date-badge{position:absolute;left:1px;top:0;width:25px;text-align:center;font-family:"Rosario",sans-serif}
.date-badge .d{display:block;height:21px;background:var(--brand-green);color:#fff;font-size:15px;font-weight:700;line-height:21px}
.date-badge .m{display:block;height:15px;background:#8a8a8a;color:#fff;font-size:9.5px;line-height:15px}
.news-item h4{position:absolute;left:53px;top:0;font-family:"Rosario",sans-serif;font-weight:400;font-size:13px;color:#333}
.news-item p{position:absolute;left:53px;top:20px;font-size:8.8px;line-height:13.5px}
.news-item .more{position:absolute;left:53px;top:52px;font-family:"Rosario",sans-serif;font-size:10px;color:#444;text-decoration:underline}
.news-sep{left:618px;top:794px;width:238px;height:1px;background:var(--rule)}

/* follow band */
.follow-band{left:0;top:907px;width:963px;height:80px;background:var(--band-grey);border-bottom:2px solid #cfcfcf}
.follow-icon{position:absolute;left:231px;top:19px;width:46px;height:46px;border-radius:50%;border:2px solid #cdcdcd;background:#f6f6f6}
.follow-icon::after{content:"";position:absolute;left:15px;top:15px;width:12px;height:12px;border-radius:50%;background:#5b5b5b}
.follow-text{position:absolute;left:291px;top:31px;font-family:"Rosario",sans-serif;font-weight:700;font-size:15px;color:#333}
.follow-text span{color:var(--brand-green);font-weight:400}

/* footer */
.footer{left:0;top:989px;width:963px;height:176px;background:repeating-linear-gradient(135deg,#333 0 2px,#2d2d2d 2px 4px)}
.foot-title{position:absolute;top:29px;font-family:"Rosario",sans-serif;font-size:16px;color:#eee}
.foot-col{position:absolute;top:56px;font-size:9.6px;line-height:14.5px;color:var(--footer-text);letter-spacing:.3px}
.foot-col dt{color:#ddd;font-weight:600}
.foot-col dd{margin-bottom:8px;color:#cfcfcf}
.foot-col .who{color:var(--link-green);font-weight:600;margin-top:2px;display:block}
.email-field{position:absolute;left:693px;top:88px;width:161px;height:24px;border-radius:3px;background:#f4f4f4;border:1px solid #ccc;font-size:9px;color:#a4a4a4;padding:6px 10px;font-family:"Open Sans",sans-serif}
.btn-subscribe{position:absolute;left:695px;top:129px;width:73px;height:19px;border-radius:3px;background:linear-gradient(#fff,#ddd);font-size:9px;font-weight:700;color:#333;display:flex;align-items:center;justify-content:center}
.base-bar{left:0;top:1165px;width:963px;height:35px;background:var(--footer-base);font-family:"Rosario",sans-serif;font-size:11px;color:#ddd}
.base-bar .copy{position:absolute;left:106px;top:10px}
.base-nav{position:absolute;right:106px;top:10px;display:flex;gap:12px}
</style>
</head>
<body>

<div class="abs topline"></div>
<header>
  <a class="abs brand" href="#"><span class="brand-mark"></span><span class="brand-name">velmor learning</span></a>
  <nav class="abs main-nav">
    <a class="current" href="#">Home</a><a href="#">About Us</a><a href="#">Courses</a><a href="#">Inspired</a><a href="#">Inspire</a><a href="#">Contact Us</a>
  </nav>
</header>

<section class="abs hero">
  <h1>I Am Velmor.</h1>
  <h2>Real HSC coaching &amp; mentoring.</h2>
  <p>The HSC help you need, in the years you need it. We offer small classes, individualised attention and genuine care for each student. It's different - in a good way. Feel free to find out more about us, and let us know if there's any way we can help you on your journey.</p>
  <a class="btn-enquire" href="#">Enquire Now</a>
  <div class="hero-art" role="img" aria-label="Illustration of maths formulas, geometric shapes, sticky notes and a wave graph above a pair of glasses"></div>
  <div class="slider-dots"><span></span><span class="on"></span><span></span><span></span></div>
</section>

<section>
  <h3 class="abs sec-title" style="left:106px;top:445px">Welcome to Velmor Learning</h3>
  <div class="abs title-rule" style="left:106px;top:477px;width:750px"></div>
  <p class="abs welcome-copy">Lorem ipsum dolor sit amet, consectetuer adipiscing elit, sed diam nonummy nibh euismod tincidunt ut laoreet dolore magna aliquam erat volutpat. Ut wisi enim ad minim veniam, quis nostrud exerci tation ullamcorper suscipit lobortis nisl ut aliquip ex ea commodo consequat. uis autem vel eum iriure dolor .in hendrerit in vulputate velit esse molestie consequat.eros et accumsan et iusto odio dignissim qui blandit praesent.</p>
  <a class="abs btn-register" href="#">Register Now</a>
  <div class="abs welcome-photo" role="img" aria-label="Photo of a student studying at a laptop in a library"></div>
</section>
<div class="abs divider"></div>

<section>
  <h3 class="abs sec-title" style="left:106px;top:674px">What our student say?</h3>
  <div class="abs title-rule" style="left:106px;top:708px;width:237px"></div>
  <div class="abs student-photo" role="img" aria-label="Portrait photo of a student"></div>
  <p class="abs col-text" style="left:171px;top:721px;width:175px">Lorem ipsum dolor sit accmet, cec dipiscing elit, sed diam. nxummy nibh euismodunt ut laoreet dolxore magna aliquam erat volutpat. Ut wisi</p>
  <p class="abs col-text" style="left:105px;top:785px;width:238px">Lorem ipsum dolor sit amet, consec dipiscing elit, sed diam. nonummy nibh euismodunt ut laoreet dolore magna. aliquam erat volutpat. Ut wisi enim ad minim veniam.</p>
  <p class="abs quote-by" style="left:106px;top:853px"><b>“Brennan Hale”</b> Westbrook HS</p>

  <h3 class="abs sec-title" style="left:362px;top:674px">Free trial lesson.</h3>
  <div class="abs title-rule" style="left:362px;top:708px;width:237px"></div>
  <div class="abs trial-box"><span class="l1">Sign Up For</span><span class="l2"><em>Free Trial Class</em> today</span></div>
  <p class="abs col-text" style="left:362px;top:785px;width:230px">Lorem ipsum dolor sit amet, consec dipiscing elit, sed diam. nonummy nibh euismodunt ut laoreet dolore magna. aliquam erat volutpat. Ut wisi enim ad minim.</p>
  <a class="abs send-link" style="left:362px;top:852px" href="#">Send an Enquiry</a>

  <h3 class="abs sec-title" style="left:618px;top:674px">News updates</h3>
  <div class="abs title-rule" style="left:618px;top:708px;width:238px"></div>
  <article class="abs news-item" style="top:722px">
    <div class="date-badge"><span class="d">15</span><span class="m">Dec</span></div>
    <h4>Brennan Hale</h4>
    <p>Lorem ipsum dolor sit amet, consec<br>dipiscing elit, sed diam.</p>
    <a class="more" href="#">Read More</a>
  </article>
  <div class="abs news-sep"></div>
  <article class="abs news-item" style="top:807px">
    <div class="date-badge"><span class="d">10</span><span class="m">Dec</span></div>
    <h4>Brennan Hale</h4>
    <p>Lorem ipsum dolor sit amet, consec<br>dipiscing elit, sed diam.</p>
    <a class="more" href="#">Read More</a>
  </article>
</section>

<section class="abs follow-band">
  <div class="follow-icon"></div>
  <p class="follow-text">Please follow <span>@Velmor Learning</span> for all future updates! 7 days ago</p>
</section>

<footer class="abs footer">
  <h4 class="foot-title" style="left:107px">Contact Details</h4>
  <dl class="foot-col" style="left:107px;top:52px">
    <dt>Street:</dt><dd>48 Larkspur Ave Kellsworth NSW 2190</dd>
    <dt>Phone:</dt><dd>(02) 5550 3821</dd>
    <dt>Email:</dt><dd>learn@velmorlearning.com.au</dd>
  </dl>
  <h4 class="foot-title" style="left:339px">SiteMap</h4>
  <ul class="foot-col" style="left:339px;top:54px;list-style:none">
    <li>Our Associates</li><li>Our Location</li><li>Our Services</li><li>Our Qualifications</li><li>Our Articles</li><li>External Page</li><li>Tell A Friend</li>
  </ul>
  <h4 class="foot-title" style="left:491px">Testimonials</h4>
  <div class="foot-col" style="left:493px;top:52px;width:165px">
    <p>Lorem Ipsum est simplement du fauxtexte employé.<span class="who">Brennan Hale</span></p>
    <p style="margin-top:13px">Lorem Ipsum est simplement du fauxtexte employé.<span class="who">Anonymus</span></p>
  </div>
  <h4 class="foot-title" style="left:696px">Sign Up for Newsletter</h4>
  <p class="foot-col" style="left:695px;top:52px;width:160px;font-size:9px">Lorem Ipsum est simplement du fauxtexte employé</p>
  <div class="email-field">Email Address</div>
  <a class="btn-subscribe" href="#">Subscribe</a>
</footer>

<div class="abs base-bar">
  <p class="copy">© Velmor Learning. All rights reserved.</p>
  <nav class="base-nav"><a href="#">Home</a><a href="#">About Us</a><a href="#">Courses</a><a href="#">Inspired</a><a href="#">Inspire</a><a href="#">Contact Us</a></nav>
</div>

</body>
</html>
```